Systems and Technology Consultants - Website

Design & Build a website for a new company which operates in the Systems and Technology space for Transportation, Government and Commercial sectors.

Overall design should be minimalist in nature.
Should also have a feed that provides news and event updates on the main page.
Logo has already been awarded and should be incorporated into the site.

We like the overall layout, functionality and simplicity of the below sites. Submitted designs could be similar to or a combination of the aspects on these sites, or perhaps a whole different concept - we are open to new ideas.
Norvique.com
Teblo.it

Update 1 Dated 27 May 2014

All I am moving away from the Teblo.it website and would like it to be more aligned with Norvique.com not only in layout but in functionality. I will be extending the deadline of this design brief for two weeks to incorporate additional requirements and will add addtional funding to the project.

Apologies for not having more information available to provide but with so many submissions its getting confusing.

Thanks Derek

Please note that the brief has been updated and the deadline has been extended.

Important: We will need two language versions of the website, English and Arabic; the website is hosted on HostPelican

Hello All, Thank you for your submissions. We have narrowed it down to the final 6 designers and I just wanted to take a moment and provide a bit of feedback regarding the concepts that we like and the modifications we are looking for. First, let me mention some of the design functions we like. - At the top of the homepage we really like the "region" or "language" tab so that the website can be viewed in both English and Arabic. - We like the homepage to have clear color variation so that the different sections of the homepage are distinct. Additionally, we like the bottom portion of the homepage to be in red. We feel that draws attention to our contact information. Again, we would like the colors to integrate black, gray-scale, red, etc. - Having a search tab at the top of the home page, or integrated into the main image, so that the site is easy to navigate. - We especially like the main image to have the scrolling tabs at the bottom so it is easy to browse the services offered (Consultancy, Solutions Architecture, Masters Systems Integration, Independent Design Review). - In regards to the services offered tab we really like the idea that a few people presented that have the outside of our logo with an icon in the middle of consultancy, solutions, etc., etc. Secondly, as mentioned in our brief we really enjoy the design of norvique site. Specially, we enjoy the strong iconic images they use, the way the tabs at the top scroll easily, and contact us page that generates an email. Lastly, I've included some photos of the concept we have been working on. What we are trying to demonstrate is how our company offers a range of services that are essentially linked together. We provide individual services that when combined present the full service package. We would like this concept to be integrated into the over concept of our website. Please feel free to ask for clarification of any of the above points or contact us if you have any additional questions. We appreciate all of your hard work and are very excited to see the updated designs. Best, Marta Vennick Quelbrant Senior Program Manager marta.vennick@quelbrant-example.com

Industry/Entity Type

Government

Font styles to use
Serif
Sans Serif

Requirements
Must have
• Must work on/adapt to various/mobile devices (responsive)
Must be simple and straightforward
Colors should be in line/matching with logo
2 language versions: English and Arabic (no Thai)
Services should be the first group/row of items after/below the main image
Note: the website will be hosted by hostpelican
Nice to have
• Submit feedback form
What's New section
The banner at the bottom of the site should not be too large; we would like a narrow one more
It would be nice if the header/top banner (with Home, About, etc. tabs) could stay in place as you scroll down (like Norvique and Chatterloop)
We will likely only use one image with a Company slogan on the Home page rather than a carousel of images to rotate through
Should not have
• This is the existing website: http://www.quelbrant-example.org
We do not like the animation, the way the banner icons/titles bounce
Not simple enough, we don't like the functionality or how pages load so slowly
We do not like the logo centered - it should be at the left
The banner and its tabs should not be towards the right, we would like them to be centered, to go all the way across and to be below the logo

```html
<!DOCTYPE html>
<html lang="en">
<head>
<meta charset="utf-8">
<title>Quelbrant International — Home</title>
<link href="https://fonts.googleapis.com/css2?family=Open+Sans:wght@400;600;700&display=swap" rel="stylesheet">
<style>
:root{
  --red:#e8202c;
  --coral:#f2595f;
  --ink:#4a4a4a;
  --grey:#8c8c8c;
  --light-grey:#b5b5b5;
  --rule:#dcdcdc;
  --footer:#333333;
  --footer-deep:#1c1c1c;
  --footer-text:#a8a8a8;
  --white:#ffffff;
}
*{margin:0;padding:0;box-sizing:border-box}
html,body{width:1090px;height:1200px;overflow:hidden;background:var(--white)}
body{position:relative;font-family:"Open Sans",Arial,sans-serif;color:var(--ink)}
.abs{position:absolute}

/* header */
.site-header{position:absolute;left:0;top:0;width:1090px;height:66px;background:var(--white)}
.brand{position:absolute;left:240px;top:12px;display:flex;align-items:center;gap:10px}
.brand-mark{width:30px;height:30px;border:4px solid var(--red)}
.brand-name{font-size:26px;font-weight:700;letter-spacing:5px;color:var(--red);line-height:1}
.main-nav{position:absolute;top:27px;right:214px;display:flex;gap:28px;font-size:9.5px;color:var(--ink);letter-spacing:.2px}
.main-nav .active{color:var(--red)}

/* hero */
.hero{position:absolute;left:0;top:66px;width:1090px;height:278px;
  background:radial-gradient(circle at 76% 45%,#c77f8f 0%,#8a3a4d 30%,transparent 60%),
             linear-gradient(90deg,#7a1822 0%,#8c2d3e 40%,#9a4a5c 70%,#b36a78 100%)}
.hero-visual{position:absolute;left:380px;top:40px;width:380px;height:226px;border-radius:6px;
  background:radial-gradient(circle at 68% 40%,#5f8fd6 0%,#2a5aa8 22%,rgba(220,220,225,.85) 36%,rgba(180,180,190,.25) 70%,transparent 100%)}

/* at a glance */
.glance-brand{position:absolute;left:0;width:1090px;top:380px;text-align:center}
.glance-mark{width:32px;height:32px;border:4px solid #9a9a9a;margin:0 auto 8px}
.glance-name{font-size:13px;font-weight:700;letter-spacing:3px;color:#8a8a8a}
.glance-sub{font-size:5.5px;letter-spacing:2px;color:#9a9a9a}
.section-rule{position:absolute;top:467px;height:1px;background:var(--rule)}
.rule-dot{position:absolute;top:464px;width:6px;height:6px;background:#cfcfcf;transform:rotate(45deg)}
.glance-title{position:absolute;left:0;width:1090px;top:460px;text-align:center;font-size:10px;font-weight:700;letter-spacing:1.5px;color:#8a8a8a}
.glance-copy{position:absolute;left:343px;top:501px;width:425px;text-align:center;font-size:8px;line-height:14.5px;color:var(--light-grey)}

.services{position:absolute;top:579px;left:0;width:1090px}
.service{position:absolute;width:100px;margin-left:-50px;text-align:center;font-size:9.5px;color:var(--ink)}
.service svg{display:block;margin:0 auto 9px}
.service.active{color:var(--red)}
.divider{position:absolute;left:240px;top:658px;width:637px;height:1px;background:var(--rule)}

/* business unit */
.unit-title{position:absolute;left:270px;top:694px;font-size:9.5px;font-weight:700;color:var(--ink);letter-spacing:.3px}
.unit-card{position:absolute;top:732px;width:136px;height:122px;border-bottom:1px solid #e2e2e2}
.unit-card.active{border-bottom:1px solid #9a9a9a}
.unit-image{position:absolute;left:4px;top:2px;width:128px;height:86px}
.unit-label{position:absolute;left:0;top:100px;width:136px;text-align:center;font-size:8.5px;color:var(--ink)}
.unit-card.active .unit-label{color:var(--red)}
.carousel-arrow{position:absolute;top:780px}

/* news strip */
.news-strip{position:absolute;left:0;top:900px;width:1090px;height:29px;background:var(--coral);display:flex;align-items:center;padding-left:240px;gap:10px;font-size:8.5px;color:var(--white)}
.news-badge{width:18px;height:18px;border-radius:50%;border:1.5px solid var(--white)}
.news-link{color:var(--white);background:rgba(255,255,255,.15)}

/* footer */
.site-footer{position:absolute;left:0;top:929px;width:1090px;height:225px;background:var(--footer);color:var(--footer-text)}
.office{position:absolute;left:239px;width:250px}
.office h4{font-size:8px;font-weight:700;color:#e6e6e6;letter-spacing:.4px;margin-bottom:4px}
.office p{font-size:7.5px;line-height:10px;width:115px}
.office .phone{position:absolute;left:133px;top:14px;font-size:7.5px;font-weight:700;color:#d8d8d8}
.office-rule{position:absolute;left:364px;width:1px;background:#555}
.footer-col h4{position:absolute;font-size:9px;font-weight:700;color:#e6e6e6;letter-spacing:.4px}
.case{position:absolute;left:517px;width:150px;font-size:7.5px;line-height:10px;color:#d0d0d0}
.case u{color:var(--white)}
.case small{display:block;font-size:5.5px;color:#8a8a8a;margin-top:5px}
.social{position:absolute;left:720px;font-size:7.5px;display:flex;align-items:center;gap:12px}
.social i{width:5px;height:5px;border-radius:50%;background:#bdbdbd}
.contact-rule{position:absolute;left:720px;width:134px;height:1px;background:#555}
.contact-email{position:absolute;left:720px;top:136px;font-size:9px;color:var(--coral)}
.bottom-bar{position:absolute;left:0;top:1154px;width:1090px;height:46px;background:var(--footer-deep);display:flex;align-items:center;padding-left:240px;gap:14px;font-size:6px;color:#777}
.bottom-brand{font-size:10px;font-weight:700;color:var(--red);letter-spacing:1px}
</style>
</head>
<body>

<header class="site-header">
  <div class="brand"><span class="brand-mark"></span><span class="brand-name">QUELBRANT</span></div>
  <nav class="main-nav">
    <span class="active">HOME</span><span>BUSINESS UNIT</span><span>SERVICES</span><span>ABOUT US</span><span>CONTACT</span>
  </nav>
</header>

<section class="hero" role="img" aria-label="Hero image: laptop beside a blue puzzle globe on a deep red background">
  <div class="hero-visual"></div>
</section>

<section class="glance">
  <div class="glance-brand">
    <div class="glance-mark"></div>
    <div class="glance-name">QUELBRANT</div>
    <div class="glance-sub">INTERNATIONAL</div>
  </div>
  <div class="section-rule" style="left:343px;width:160px"></div>
  <div class="rule-dot" style="left:500px"></div>
  <div class="section-rule" style="left:614px;width:158px"></div>
  <div class="rule-dot" style="left:609px"></div>
  <h2 class="glance-title">AT A GLANCE</h2>
  <p class="glance-copy">Quelbrant is a joint venture between ravello construction, marden worldwide and tessler engineering &amp; management company founded in meridian city in 2003 and orbel electrical construction company founded in san francisco, california in 2001. developed by former kestrel telecom, harrowgate and lindqvist and morrow employees with over 30 years experience in engineering and construction of systems around the globe.</p>

  <div class="services">
    <div class="service" style="left:389px">
      <svg width="30" height="30" viewBox="0 0 30 30"><circle cx="15" cy="15" r="14" fill="none" stroke="#555" stroke-width="1.5"/><path d="M8 11h4l6 8h4M8 19h4l6-8h4M20 9l2 2-2 2M20 17l2 2-2 2" fill="none" stroke="#555" stroke-width="1.5"/></svg>Consulting</div>
    <div class="service" style="left:473px">
      <svg width="30" height="30" viewBox="0 0 30 30"><circle cx="15" cy="15" r="14" fill="none" stroke="#555" stroke-width="1.5"/><path d="M15 7c3 3 3 8 2 11h-4c-1-3-1-8 2-11zM13 18l-3 4M17 18l3 4" fill="#555" stroke="#555" stroke-width="1"/></svg>Engineering</div>
    <div class="service" style="left:557px">
      <svg width="30" height="30" viewBox="0 0 30 30"><circle cx="15" cy="15" r="14" fill="none" stroke="#555" stroke-width="1.5"/><path d="M9 21h12M10 9v12M12 12h5M12 15h7M12 18h4" fill="none" stroke="#555" stroke-width="2"/></svg>Construction</div>
    <div class="service" style="left:642px">
      <svg width="30" height="30" viewBox="0 0 30 30"><circle cx="15" cy="15" r="14" fill="none" stroke="#555" stroke-width="1.5"/><circle cx="15" cy="15" r="6.5" fill="#555"/><path d="M15 15V8.5A6.5 6.5 0 0 1 21.5 15z" fill="#fff"/></svg>Operations</div>
    <div class="service active" style="left:726px">
      <svg width="30" height="30" viewBox="0 0 30 30"><circle cx="15" cy="15" r="14" fill="none" stroke="#e8202c" stroke-width="1.5"/><path d="M12 8v14M18 8v14M10 8h4M16 8h4" fill="none" stroke="#e8202c" stroke-width="2"/></svg>Maintenance</div>
  </div>
  <div class="divider"></div>
</section>

<section class="business-unit">
  <h3 class="unit-title">BUSINESS UNIT</h3>
  <svg class="carousel-arrow" style="left:238px" width="10" height="16" viewBox="0 0 10 16"><path d="M8 1L2 8l6 7" fill="none" stroke="#aaa" stroke-width="1.2"/></svg>
  <svg class="carousel-arrow" style="left:868px" width="10" height="16" viewBox="0 0 10 16"><path d="M2 1l6 7-6 7" fill="none" stroke="#aaa" stroke-width="1.2"/></svg>

  <div class="unit-card" style="left:268px">
    <div class="unit-image" role="img" aria-label="Photo of a blue circuit board" style="background:linear-gradient(135deg,#0a3a7a,#2f8fe0 55%,#0b2d66)"></div>
    <div class="unit-label">Systems Design &amp; Engineering</div>
  </div>
  <div class="unit-card active" style="left:416px">
    <div class="unit-image" role="img" aria-label="Image of a blue project flowchart" style="background:linear-gradient(135deg,#0d2a6e,#3b6fd0 55%,#0e2a6b)"></div>
    <div class="unit-label">Systems Project Management</div>
  </div>
  <div class="unit-card" style="left:564px">
    <div class="unit-image" role="img" aria-label="Image of a radio tower with signal rings" style="background:radial-gradient(circle at 50% 55%,#37b6e8,#0d4c7e 45%,#06203d)"></div>
    <div class="unit-label">Radio Area Networks</div>
  </div>
  <div class="unit-card" style="left:711px">
    <div class="unit-image" role="img" aria-label="Photo of rolled blueprints" style="background:linear-gradient(135deg,#9fc1e6,#4f88c6 50%,#2a5c98)"></div>
    <div class="unit-label">Systems Construction Management</div>
  </div>
</section>

<aside class="news-strip">
  <span class="news-badge"></span>
  <span>@quelbrantintl: <span class="news-link">http://example.org/quelbrant/updates/2/</span> Follow and we'll Return the favour. 1 Days ago</span>
</aside>

<footer class="site-footer">
  <div class="office-rule" style="top:46px;height:44px"></div>
  <div class="office-rule" style="top:104px;height:44px"></div>
  <div class="office-rule" style="top:164px;height:44px"></div>

  <div class="office" style="top:45px"><h4>HEADQUARTERS</h4><p>14 lanterna rd, east quarter, meridian city 20410</p><span class="phone">+(00)-02-555-0148-1</span></div>
  <div class="office" style="top:104px"><h4>HARBOUR BRANCH</h4><p>88/2 harbour house, quayside rd, west wharf, meridian city 20115</p><span class="phone">+(00)-02-555-0172</span></div>
  <div class="office" style="top:164px"><h4>COASTLINE BRANCH</h4><p>31/7 coastline ave, sandmere, port olvey 30260</p><span class="phone">+(00)-038-555-019</span></div>

  <div class="footer-col">
    <h4 style="left:517px;top:44px">CASE STUDY</h4>
    <div class="case" style="top:65px">Lorem Ipsum is <u>simply dummy text</u> of the printing and typesetting industry.<small>25 June 2015</small></div>
    <div class="case" style="top:109px">Lorem Ipsum is <u>simply dummy text</u> of the printing and typesetting industry.<small>25 June 2015</small></div>
    <div class="case" style="top:153px">Lorem Ipsum is <u>simply dummy text</u> of the printing and typesetting industry.<small>25 June 2015</small></div>
  </div>

  <div class="footer-col">
    <h4 style="left:720px;top:44px">GET IN TOUCH</h4>
    <div class="social" style="top:65px"><i></i>chirper.example/quelbrant</div>
    <div class="social" style="top:82px"><i></i>chatterloop.example/pages/quelbrant</div>
    <div class="social" style="top:98px"><i></i>proflink.example/company/quelbrant</div>
    <div class="contact-rule" style="top:125px"></div>
    <div class="contact-email">Email: info@quelbrant-example.org</div>
    <div class="contact-rule" style="top:162px"></div>
  </div>
</footer>

<div class="bottom-bar">
  <span class="bottom-brand">QUELBRANT</span>
  <span>© 2014. All Right Reserved.</span>
</div>

</body>
</html>
```